Spiritual Healing bussiness needs logo/business card

Simple, clean looking logo/card
For spiritual business with healing services and occult rituals

Contact Information for Business Card

Needs my name: Tobin Varley
Business name: Lantern Healing Shop
Services provided and worded in this way:

Reiki Healing
Tarot
Oils
Rituals Of Change

Can look occult like but with light energy.

Colors
0255a3
3276b5
85abd2
33a6d7
85cae6
0292cd

```html
<!DOCTYPE html>
<html lang="en">
<head>
<meta charset="utf-8">
<title>Tobin Varley – Lantern Healing Shop</title>
<link rel="stylesheet" href="https://fonts.googleapis.com/css2?family=Marcellus&display=swap">
<style>
  :root {
    --side-blue: #355f9e;
    --panel-blue: #4172b6;
    --sage: #7ac29a;
    --white: #ffffff;
  }
  html, body {
    margin: 0;
    padding: 0;
    width: 1200px;
    height: 777px;
    overflow: hidden;
    background: var(--side-blue);
  }
  .card {
    position: relative;
    width: 1200px;
    height: 777px;
    overflow: hidden;
    background: var(--side-blue);
    font-family: "Marcellus", serif;
  }
  .corner-shapes {
    position: absolute;
    inset: 0;
  }
  .center-panel {
    position: absolute;
    left: 288px;
    top: 0;
    width: 624px;
    height: 777px;
    background: var(--panel-blue);
    text-align: center;
  }
  .owner-name {
    margin: 0;
    position: absolute;
    top: 38px;
    left: 0;
    right: 0;
    color: var(--white);
    font-size: 58px;
    font-weight: 400;
    letter-spacing: 2px;
    line-height: 1;
  }
  .brand {
    position: absolute;
    top: 230px;
    left: 0;
    right: 0;
    display: flex;
    flex-direction: column;
    align-items: center;
    gap: 22px;
  }
  .brand-dot {
    width: 44px;
    height: 44px;
    border-radius: 50%;
    background: var(--sage);
  }
  .brand-name {
    color: var(--sage);
    font-size: 36px;
    line-height: 1;
  }
  .services {
    list-style: none;
    margin: 0;
    padding: 0;
    position: absolute;
    top: 505px;
    left: 0;
    right: 0;
    color: var(--sage);
    font-size: 53px;
    line-height: 78px;
  }
</style>
</head>
<body>
  <div class="card">
    <svg class="corner-shapes" width="1200" height="777" viewBox="0 0 1200 777" aria-hidden="true">
      <ellipse cx="330" cy="790" rx="150" ry="310" fill="var(--sage)"/>
      <ellipse cx="870" cy="790" rx="150" ry="310" fill="var(--sage)"/>
    </svg>
    <div class="center-panel">
      <h1 class="owner-name">TOBIN VARLEY</h1>
      <div class="brand">
        <span class="brand-dot"></span>
        <span class="brand-name">Lantern Healing Shop</span>
      </div>
      <ul class="services">
        <li>Reiki Healing</li>
        <li>Tarot - Oils</li>
        <li>Rituals Of Change</li>
      </ul>
    </div>
  </div>
</body>
</html>
```